Luxury free range egg pack for eggs with golden orange yolks

We are looking for a new faced egg pack for one of our brands called Meadow Crest which is free range eggs with golden yolks.
This will be for a more up market target audience.

Target Market(s)

Luxury egg purchase

Industry/Entity Type

Egg production

Font styles to use
Decorative
Script

Colors
F0912C
F2A743
F7CA91
FBE8D2
FDF5EE

Requirements
Must have
• Orange or gold colouring in place in the theme

```html
<!DOCTYPE html>
<html lang="en">
<head>
<meta charset="utf-8">
<title>Meadow Crest Free Range Egg Pack Label</title>
<link rel="stylesheet" href="https://fonts.googleapis.com/css2?family=Rye&family=Courgette&family=Cinzel:wght@700&family=Oswald:wght@500&display=swap">
<style>
  :root {
    --stage: #e9b48c;
    --orange: #f0912c;
    --amber: #f2a743;
    --sand: #f7ca91;
    --cream: #fbe8d2;
    --ivory: #fdf5ee;
    --brown: #6b1f1a;
    --tan: #b9785c;
    --gold-dark: #a86a12;
    --gold-light: #ffe9a6;
  }
  * { margin: 0; padding: 0; box-sizing: border-box; }
  html, body { width: 1200px; height: 576px; overflow: hidden; }
  body { background: var(--stage); position: relative; }

  .pack-label {
    position: absolute; left: 150px; top: 75px;
    width: 900px; height: 426px;
    background: linear-gradient(180deg, #c98a6c, var(--tan) 60%, #a7654b);
    border-radius: 4px;
  }
  .gold-frame {
    position: absolute; left: 22px; top: 18px; right: 22px; bottom: 18px;
    border-radius: 26px;
    padding: 9px;
    background: linear-gradient(135deg, var(--gold-light), var(--amber) 30%, var(--gold-dark) 55%, var(--gold-light) 80%, var(--amber));
  }
  .label-field {
    position: relative; width: 100%; height: 100%;
    border-radius: 18px;
    background: radial-gradient(ellipse at 50% 42%, var(--cream) 0%, var(--sand) 45%, #dca27a 100%);
    border: 3px solid var(--brown);
  }
  .key-band {
    position: absolute; left: 18px; right: 18px; height: 14px;
    background: linear-gradient(180deg, var(--gold-light), var(--amber), var(--gold-dark));
  }
  .key-band--top { top: 18px; }
  .key-band--bottom { bottom: 46px; }

  .flourish {
    position: absolute; left: 50%; top: 48px; width: 150px; height: 40px;
    transform: translateX(-50%);
    background: linear-gradient(180deg, var(--gold-light), var(--amber));
    border-radius: 20px 20px 4px 4px;
    opacity: .75;
  }
  .brand {
    position: absolute; left: 0; right: 0; top: 104px;
    display: flex; align-items: center; justify-content: center; gap: 12px;
  }
  .brand-dot {
    width: 34px; height: 34px; border-radius: 50%;
    background: var(--amber);
  }
  .brand-name {
    font-family: "Rye", serif; font-size: 30px; color: var(--brown);
  }
  .product-title {
    position: absolute; left: 0; right: 0; top: 188px;
    text-align: center;
    font-family: "Rye", serif; font-size: 46px; letter-spacing: 1px;
    color: var(--amber);
    text-shadow: 2px 2px 0 var(--brown);
  }
  .title-rule {
    position: absolute; left: 50%; top: 248px; width: 300px; height: 2px;
    transform: translateX(-50%);
    background: linear-gradient(90deg, transparent, var(--brown), transparent);
  }
  .tagline {
    position: absolute; left: 0; right: 0; top: 256px;
    text-align: center;
    font-family: "Courgette", cursive; font-size: 22px;
    color: var(--brown);
  }
  .grade, .count {
    position: absolute; top: 262px;
    font-family: "Cinzel", serif; font-size: 17px; color: var(--ivory);
    text-shadow: 1px 1px 0 var(--brown);
  }
  .grade { left: 26px; }
  .count { right: 26px; }
  .count-number { font-size: 30px; }
  .system-codes {
    position: absolute; left: 0; right: 0; bottom: 12px;
    display: flex; justify-content: center; align-items: center; gap: 10px;
    font-family: "Oswald", sans-serif; font-size: 17px; letter-spacing: 1px;
    color: var(--ivory);
  }
  .code-dot {
    width: 9px; height: 9px; border-radius: 50%;
    background: var(--orange);
  }
</style>
</head>
<body>
  <section class="pack-label">
    <div class="gold-frame">
      <div class="label-field">
        <div class="key-band key-band--top" role="img" aria-label="Gold Greek key border pattern"></div>
        <div class="flourish" role="img" aria-label="Gold scroll ornament"></div>

        <div class="brand">
          <span class="brand-dot"></span>
          <span class="brand-name">Meadow Crest</span>
        </div>

        <h1 class="product-title">Free Range Egg</h1>
        <div class="title-rule"></div>
        <p class="tagline">With Golden Orange Yolks</p>

        <p class="grade">Class A</p>
        <p class="count"><span class="count-number">6</span> Large Egg</p>

        <div class="key-band key-band--bottom" role="img" aria-label="Gold Greek key border pattern"></div>

        <p class="system-codes">
          <span>0 = ORGANIC</span><span class="code-dot"></span>
          <span>1 = F/RANGE</span><span class="code-dot"></span>
          <span>2 = BARN</span><span class="code-dot"></span>
          <span>3 = CAGE</span>
        </p>
      </div>
    </div>
  </section>
</body>
</html>
```